New website for gluNote

We are looking to redesign our e-newsletter gluNote. This a monthly newsletter that publishes the latest research and product news in the diabetes field for people with diabetes. Our current website is here: www.glunote.us.

The parameters are the new site must incorporate our logo, must use the same colors (variation in shade and adding some colors is fine, but the initial pallet should stay) and must be in 1024 by 768 px. It is crucially important that the font in the new design be easily readable (dark, well spaced). If it could be a layered PSD that would be ideal. We have attached 2 sketches of our own brainstorming for a potential lay-out for the home and a new issue page, but these are very rough and should not in any way limit the true designers out there.

We're envisioning a very polished, sophisticated looking magazine-esque site that presents a lot of information. When we were brainstorming for new site ideas we looked at major monthly publications such as the Harbor Monthly (www.harbormonthly.com) or Silver Quill (www.sq.com). Like these sites we would still like to feature much of our newest content on the front page, but in a manner that makes good use of space and feels uncluttered. Information needs to be clearly labeled and easy to find. In terms of the overall tone of the website, we do very much want it to be nice and elegant looking site, and one that is targeting a smart, engaged audience.
Updates

Reason: I didn't realize I'd made this due on a Sunday. Please take a couple of extra days everyone.

Industry/Entity Type

News

Requirements
Must have
• The logo. The same color scheme we currently use
Nice to have
• We like the idea of having a featured content box, of using hover buttons on top for our various sections, and potentially using a 3 column setup. However, we are not web designers, so the designer can use these suggestions at their discretion.

```html
<!DOCTYPE html>
<html lang="en">
<head>
<meta charset="utf-8">
<title>gluNote – research and product news for people with diabetes</title>
<link rel="stylesheet" href="https://fonts.googleapis.com/css2?family=Gelasio:wght@400;700&family=PT+Sans:wght@400;700&display=swap">
<style>
:root{
  --teal:#5fb3ac;
  --brown:#3b2415;
  --tag:#6b5a4e;
  --blue:#1b7cc4;
  --orange:#f08a00;
  --grey-text:#8a8a8a;
  --body:#555;
  --dark:#222;
  --panel:#e7e7e7;
  --line:#c9c9c9;
  --page-bg:#eeeeee;
}
*{box-sizing:border-box;margin:0;padding:0}
html,body{width:1092px;height:1200px;overflow:hidden;background:var(--page-bg)}
.stage{position:absolute;left:0;top:0;width:1048px;height:1152px;transform:scale(1.042);transform-origin:0 0;font-family:"Gelasio",Georgia,serif;color:var(--body)}
.page{position:absolute;left:26px;top:16px;width:996px;height:1124px;background:#fff;border:1px solid #ddd}
.abs{position:absolute}

/* header */
.brand{left:50px;top:28px;font-family:"PT Sans",sans-serif;font-size:92px;line-height:1;color:var(--teal);letter-spacing:-2px}
.tagline{left:445px;top:66px;font-size:15px;line-height:19px;color:var(--tag)}
.promo{left:746px;top:25px;width:270px;height:108px;border:1px solid #cfcfcf;border-radius:8px;background:linear-gradient(#fafafa,#e4e4e4);overflow:hidden}
.promo-cover{left:7px;top:6px;width:76px;height:96px;background:linear-gradient(#c9dce8,#8fa8a0 70%,#9cc9c2)}
.promo-title{left:92px;top:6px;font-family:"PT Sans",sans-serif;font-size:17px;color:var(--orange)}
.promo-text{left:92px;top:30px;font-family:"PT Sans",sans-serif;font-size:13px;line-height:16px;color:var(--dark)}
.promo-sub{left:92px;top:70px;font-family:"PT Sans",sans-serif;font-size:11px;color:#555}
.promo-link{left:92px;top:87px;font-family:"PT Sans",sans-serif;font-size:10px;color:var(--blue);text-decoration:underline}
.ribbon{right:-34px;top:14px;width:130px;height:20px;background:#f5b400;color:#5a3b00;font-family:"PT Sans",sans-serif;font-size:10px;line-height:20px;text-align:center;transform:rotate(45deg)}

.nav{left:26px;top:145px;width:764px;height:28px;display:flex;background:linear-gradient(#fff,#ececec);border-bottom:1px solid #ddd;font-family:"PT Sans",sans-serif;font-size:13.5px;color:#333}
.nav span{display:flex;align-items:center;justify-content:center;border-right:1px solid #d5d5d5}
.nav .active{background:var(--teal);color:#1f3f3c}
.signup{left:793px;top:139px;width:231px;height:41px;border-radius:5px;background:linear-gradient(#2a98e8,#0b63b5);color:#fff;font-family:"PT Sans",sans-serif;text-align:center}
.signup b{display:block;font-weight:400;font-size:16px;margin-top:3px}
.signup small{font-size:11.5px}

.col-rule{left:702px;top:185px;width:1px;height:912px;background:var(--line)}
.hrule{left:42px;width:660px;height:1px;background:var(--line)}

/* feature */
.feature-img{left:50px;top:201px;width:200px;height:249px;background:linear-gradient(#dfe4ea 0,#c2ccd4 40%,#6f7d6a 65%,#9bcfc6 88%)}
.feature-title{left:264px;top:199px;font-family:"PT Sans",sans-serif;font-weight:700;font-size:25px;color:var(--teal)}
.feature-sub{left:270px;top:234px;font-family:"PT Sans",sans-serif;font-weight:400;font-size:19px;color:var(--blue)}
.feature-label{left:271px;top:266px;font-size:15px;color:var(--grey-text);text-decoration:underline}
.feature-body{left:271px;top:302px;width:424px;font-size:12.8px;line-height:17px;color:var(--grey-text)}
.feature-body p+p{margin-top:15px}
.more{font-size:13px;color:var(--orange);text-decoration:underline}

.issue-title{left:53px;top:482px;font-weight:400;font-size:26px;color:var(--blue)}
.download{left:542px;top:492px;font-size:12px;color:var(--orange);text-decoration:underline}

.story-img{border:1px solid #333}
.story-kicker{font-size:11.5px;color:var(--orange);text-decoration:underline}
.story-text{font-size:13.2px;line-height:17px;color:var(--body)}

/* sidebar */
.search{left:717px;top:204px;width:298px;height:38px;border:1px solid #ccc;background:#fff}
.search-field{left:6px;top:6px;width:208px;height:24px;border:1px solid #ccc;font-family:"PT Sans",sans-serif;font-size:14px;line-height:22px;padding-left:3px;color:#222}
.search-btn{left:220px;top:7px;width:70px;height:21px;background:#e3e3e3;font-family:"PT Sans",sans-serif;font-size:10px;letter-spacing:1px;line-height:21px;text-align:center;color:#777}
.tabs{left:716px;top:257px;display:flex;font-size:11.5px;color:#333}
.tabs span{height:35px;display:flex;align-items:center;justify-content:center;background:#f3f3f3;border:1px solid #ddd;margin-right:3px;white-space:nowrap}
.tabs .on{background:#d3d3d3}
.popular{left:717px;top:292px;width:295px;height:228px;background:var(--panel);padding:16px 10px 0 5px}
.popular ol{list-style:none;font-size:11.3px;line-height:14px;color:var(--grey-text)}
.popular li{display:flex;margin-bottom:9px}
.popular li i{font-style:normal;color:var(--blue);width:15px;flex:none}

.social{left:717px;top:556px;width:295px;height:390px;background:var(--panel)}
.social-head{left:11px;top:9px;font-family:"PT Sans",sans-serif;font-size:17px;color:var(--blue)}
.follow-badge{left:72px;top:4px}
.account{left:16px;top:44px;display:flex;align-items:center;gap:6px}
.account-mark{font-family:"PT Sans",sans-serif;font-size:20px;color:var(--teal)}
.account-name{font-family:"PT Sans",sans-serif;font-size:11px;line-height:13px;color:#444}
.account-name b{display:block;font-size:16px;font-weight:400;color:#111}
.tweet{left:12px;width:270px;font-size:12.8px;line-height:17px;color:var(--dark);border-bottom:1px solid #aaa;padding:0 0 6px 10px}
.tweet a{color:var(--orange)}
.tweet small{display:block;font-size:11.5px;color:var(--orange)}
.social-foot{left:22px;top:350px;font-family:"PT Sans",sans-serif;font-size:20px;color:#6a8ee8}
.join{left:162px;top:356px;font-size:12.5px;color:#3b6fd6}

.subscribe{left:717px;top:962px;width:295px;height:124px;background:var(--panel)}
.subscribe h3{left:12px;top:6px;font-weight:400;font-size:15.5px;color:var(--dark)}
.sub-item{text-align:center;font-size:12px;color:var(--dark)}
.sub-item span{display:block;width:40px;height:40px;margin:0 auto 6px;border-radius:3px}

.footer{left:33px;top:1100px;width:987px;height:32px;background:#ebebeb;border-radius:4px;font-size:12px;color:#333;line-height:32px;padding-left:15px}
.footer .sep{margin:0 6px;color:#888}
.copy{right:14px;top:0;font-size:9.5px;color:#666}
</style>
</head>
<body>
<div class="stage">
  <div class="page"></div>

  <header>
    <div class="abs brand">gluNote</div>
    <div class="abs tagline">research and product<br>news for people<br>with diabetes</div>
    <div class="abs promo">
      <div class="abs promo-cover" role="img" aria-label="Report cover: mother and daughter by the sea"></div>
      <div class="abs promo-title">Free Report:</div>
      <div class="abs promo-text">Charting a Cure<br>For Type 1 Diabetes:</div>
      <div class="abs promo-sub">When Will the Wait End?</div>
      <div class="abs promo-link">Click here to read our new report!</div>
      <div class="abs ribbon">Subscribe Now</div>
    </div>
    <nav class="abs nav">
      <span class="active" style="width:90px">Home</span>
      <span style="width:144px">About Us</span>
      <span style="width:122px">Sign-up</span>
      <span style="width:187px">In this issue/archives</span>
      <span style="width:110px">Blog</span>
      <span style="width:111px;border:0">Help</span>
    </nav>
    <div class="abs signup"><b>sign-up for gluNote</b><small>Click here to sign-up for gluNote. It's free!</small></div>
  </header>

  <div class="abs col-rule"></div>

  <main>
    <div class="abs feature-img" role="img" aria-label="Report cover: mother and daughter looking out over the bay"></div>
    <h1 class="abs feature-title">Charting a Cure for Type 1 Diabetes</h1>
    <h2 class="abs feature-sub">When Will the Wait End?</h2>
    <div class="abs feature-label">About the Report</div>
    <div class="abs feature-body">
      <p>Every person touched by diabetes wants to know when there will be a cure. A lot of work is going on, but what are the chances of a breakthrough? Charting a Cure for Type 1 Diabetes is gluNote's comprehensive overview of where we are and where we're headed in that search.</p>
      <p>Rich in detail and written for patients and their families, the report features the latest information on the most promising ...</p>
      <p style="margin-top:9px"><span class="more">More »</span></p>
    </div>

    <div class="abs hrule" style="top:473px"></div>
    <h2 class="abs issue-title">current issue - #34 - july 2011</h2>
    <div class="abs download">Download Printable Version</div>

    <div class="abs story-img" style="left:55px;top:546px;width:82px;height:114px;background:linear-gradient(#c9c4bb,#8a7d70)" role="img" aria-label="Portrait of the editor"></div>
    <div class="abs" style="left:148px;top:544px;width:232px"><div class="story-kicker">from the editor</div><div class="story-text">Kara muses on the search for a cure, and what we have in the meantime.</div></div>

    <div class="abs story-img" style="left:393px;top:545px;width:82px;height:61px;background:linear-gradient(#d9c3a8,#9a7a5a)" role="img" aria-label="Photo of a mother and daughter"></div>
    <div class="abs" style="left:487px;top:544px;width:205px"><div class="story-kicker">learning curve</div><div class="story-text">Where are we today in the quest for a cure?</div></div>

    <div class="abs story-img" style="left:56px;top:711px;width:82px;height:58px;background:linear-gradient(#3c8ed8,#5d5a40)" role="img" aria-label="Illustration of an insulin pump and sensor worn on the body"></div>
    <div class="abs" style="left:150px;top:707px;width:228px"><div class="story-kicker">new now next</div><div class="story-text">An update on the artificial pancreas, new drugs in development, Glyvantra's approval in Europe, and more...</div></div>

    <div class="abs story-img" style="left:396px;top:710px;width:80px;height:100px;background:linear-gradient(#a8a4a0,#4f4a46)" role="img" aria-label="Portrait of the columnist"></div>
    <div class="abs" style="left:491px;top:709px;width:180px"><div class="story-kicker">pump &amp; sensor notes</div><div class="story-text">What if a closed-loop system used three hormones, instead of one? Gavin Shore discusses the possibility.</div></div>

    <div class="abs hrule" style="top:849px"></div>
  </main>

  <aside>
    <div class="abs search">
      <div class="abs search-field">Search</div>
      <div class="abs search-btn">SEARCH</div>
    </div>
    <div class="abs tabs">
      <span class="on" style="width:83px">Most Popular</span>
      <span style="width:78px">Most Recent</span>
      <span style="width:128px">Editors Recommended</span>
    </div>
    <div class="abs popular">
      <ol>
        <li><i>1.</i>Every person touched by diabetes wants to know when there will be a cure.</li>
        <li><i>2.</i>A lot of work is going on, but what are the chances of a breakthrough? Charting a Cure.</li>
        <li><i>3.</i>Type 1 Diabetes is gluNote's comprehensive overview of where we are and where we're headed in that search.</li>
        <li><i>4.</i>Rich in detail and written for patients and their families, the report features the latest information on the most promising ...</li>
      </ol>
      <div style="margin:10px 0 0 15px"><span class="more" style="font-size:12.5px">More »</span></div>
    </div>

    <div class="abs social">
      <div class="abs social-head">Chatterly</div>
      <svg class="abs follow-badge" width="62" height="26" viewBox="0 0 62 26"><rect x="1" y="3" width="58" height="20" rx="4" fill="#fff6c8" stroke="#c9a200"/><text x="30" y="17" text-anchor="middle" font-family="PT Sans, sans-serif" font-size="11" font-weight="700" fill="#333">Follow</text></svg>
      <div class="abs account"><span class="account-mark">gluNote</span><span class="account-name">gluNote<b>gluNoteNews</b></span></div>
      <div class="abs tweet" style="top:92px">@<a>MaraNayland</a> is prescribed all over, off-label, for obesity, often in combo<small>4 hours ago · reply · retweet · favorite</small></div>
      <div class="abs tweet" style="top:162px">@<a>MarcRowanCEO</a> the link isn't working, ack, and we really wanna read it!<small>5 hours ago · reply · retweet · favorite</small></div>
      <div class="abs tweet" style="top:232px">@<a>mattheweller</a> Think he's saying in order 4 #glif 2b approved, prosp RCT needed, n=30k to 100k patients-he actually seems 2 consider tenable<small>16 hours ago · reply · retweet · favorite</small></div>
      <div class="abs social-foot">Chatterly</div>
      <div class="abs join">Join the conversation</div>
    </div>

    <div class="abs subscribe">
      <h3 class="abs">subscribe and follow us:</h3>
      <div class="abs sub-item" style="left:18px;top:42px;width:44px"><span style="background:#f08a20"></span>RSS</div>
      <div class="abs sub-item" style="left:88px;top:42px;width:70px"><span style="background:#4aa3df"></span>Chatterly</div>
      <div class="abs sub-item" style="left:168px;top:42px;width:70px"><span style="background:#3b5c9e"></span>Friendbook</div>
    </div>
  </aside>

  <footer class="abs footer">
    home<span class="sep">|</span>privacy policy<span class="sep">|</span>editorial policy/disclosure<span class="sep">|</span>contact us
    <span class="abs copy">© 2011 gluNote®. All rights reserved</span>
  </footer>
</div>
</body>
</html>
```